Request for Business Card Design

Hi. My name is Marlene, I am looking for a new business card design for my company, Quarrow Signal Instruments, LLC. I really like the design you did for Tarsel Venture and was hoping you could do something similar using our full logo and our mark. I am also open to any raised texture design using our mark. I have attached our full logo, which would need to be somewhere on the card, as well as the mark in both outline and full form, as well as our brand colors / guide. The card does not have to be white, as long as our logo and mark appear. I actually like darker colored business cards more, but am open to all options. If you are interested in working with me, please let me know. We would also take the business card design into letterhead design if you can do that.

```html
<!DOCTYPE html>
<html lang="en">
<head>
<meta charset="utf-8">
<title>Quarrow Signal Instruments – Business Card</title>
<link rel="stylesheet" href="https://fonts.googleapis.com/css2?family=Exo+2:wght@800&family=Arimo:wght@400;700&display=swap">
<style>
  :root {
    --stage: #111213;
    --card: #232323;
    --brand-blue: #0b88b3;
    --white: #f4f4f4;
    --muted: #e2e2e2;
    --emboss: #2b2b2b;
  }
  * { box-sizing: border-box; margin: 0; padding: 0; }
  html, body { width: 1200px; height: 963px; overflow: hidden; }
  body {
    background: var(--stage);
    display: flex;
    align-items: center;
    justify-content: center;
    gap: 40px;
    font-family: "Arimo", Arial, sans-serif;
  }
  .card {
    position: relative;
    width: 540px;
    height: 309px;
    background: var(--card);
    border-radius: 22px;
    border-bottom: 3px solid var(--brand-blue);
    border-right: 2px solid var(--brand-blue);
    overflow: hidden;
  }
  .wordmark {
    display: flex;
    align-items: center;
    gap: 16px;
  }
  .wordmark__dot {
    width: 58px; height: 58px;
    border-radius: 50%;
    background: var(--brand-blue);
    flex: none;
  }
  .wordmark__name {
    font-family: "Exo 2", "Arial Black", sans-serif;
    font-weight: 800;
    color: var(--white);
    line-height: 1;
  }
  .wordmark__title { font-size: 44px; letter-spacing: 4px; display: block; }
  .wordmark__tagline { font-size: 12.5px; letter-spacing: 1.6px; display: block; margin-top: 6px; }

  .card--front { display: flex; align-items: center; justify-content: center; }

  .card--back .wordmark { position: absolute; left: 34px; top: 30px; }
  .card--back .wordmark__title { font-size: 36px; letter-spacing: 3px; }
  .card--back .wordmark__tagline { font-size: 10.5px; letter-spacing: 1.3px; }

  .raised-mark {
    position: absolute;
    right: -30px; top: 60px;
    width: 240px; height: 240px;
    border-radius: 50%;
    background: radial-gradient(circle at 40% 35%, #303030, var(--emboss) 60%, #1e1e1e);
    box-shadow: inset 2px 2px 3px rgba(255,255,255,0.06), inset -3px -3px 6px rgba(0,0,0,0.4);
  }
  .person { position: absolute; left: 34px; top: 118px; }
  .person__name {
    font-weight: 700; font-size: 19px; color: var(--brand-blue);
    text-transform: uppercase; letter-spacing: 0.5px;
  }
  .person__role { font-size: 14px; color: var(--muted); margin-top: 2px; }
  .divider {
    position: absolute; left: 34px; top: 172px;
    width: 400px; height: 1px; background: var(--brand-blue);
  }
  .contacts { position: absolute; left: 34px; top: 188px; list-style: none; }
  .contacts li {
    display: flex; align-items: center; gap: 10px;
    font-size: 14px; color: var(--white); margin-bottom: 8px;
  }
  .contacts svg { width: 14px; height: 14px; flex: none; }
  .address {
    position: absolute; right: 40px; bottom: 26px;
    font-size: 14px; color: var(--white); text-align: right; line-height: 1.35;
  }
</style>
</head>
<body>
  <article class="card card--front">
    <div class="wordmark">
      <span class="wordmark__dot"></span>
      <span class="wordmark__name">
        <span class="wordmark__title">QUARROW</span>
        <span class="wordmark__tagline">SIGNAL INSTRUMENTS</span>
      </span>
    </div>
  </article>

  <article class="card card--back">
    <div class="raised-mark" role="img" aria-label="Raised brand mark area"></div>
    <div class="wordmark">
      <span class="wordmark__name">
        <span class="wordmark__title">QUARROW</span>
        <span class="wordmark__tagline">SIGNAL INSTRUMENTS</span>
      </span>
    </div>
    <div class="person">
      <p class="person__name">Elias Brandt</p>
      <p class="person__role">Manager</p>
    </div>
    <div class="divider"></div>
    <ul class="contacts">
      <li>
        <svg viewBox="0 0 24 24" fill="var(--brand-blue)"><path d="M6.6 10.8a15 15 0 0 0 6.6 6.6l2.2-2.2a1 1 0 0 1 1-.25 11 11 0 0 0 3.6.6 1 1 0 0 1 1 1V20a1 1 0 0 1-1 1A17 17 0 0 1 3 4a1 1 0 0 1 1-1h3.5a1 1 0 0 1 1 1c0 1.25.2 2.45.6 3.6a1 1 0 0 1-.25 1z"/></svg>
        123-456-2100
      </li>
      <li>
        <svg viewBox="0 0 24 24" fill="none" stroke="var(--brand-blue)" stroke-width="2"><rect x="3" y="5" width="18" height="14" rx="1"/><path d="M3 6l9 7 9-7"/></svg>
        hello@quarrowsignal.com
      </li>
      <li>
        <svg viewBox="0 0 24 24" fill="none" stroke="var(--brand-blue)" stroke-width="2"><circle cx="12" cy="12" r="9"/><path d="M3 12h18M12 3c3 3 3 15 0 18M12 3c-3 3-3 15 0 18"/></svg>
        www.quarrowsignal.com
      </li>
    </ul>
    <p class="address">Your Address, City<br>State, Zip 0000</p>
  </article>
</body>
</html>
```